New Business Card Design Project LORVANTI-Italy

we are LORVANTI-Italy
our company in the market for 3 years we are luxury cosmetic company and its about time for a facelift :)
i will like to have elegant luxurious and unique business card
that will give the person that get it a unique, luxurious and elegant impression
I'm VERY OPEN FOR NEW IDEAS , even duo i add a few files of things that i see on line and i like them

i add my logo as well
my website is LORVANTI.COM
(if you would like to see the main style that we have)

Target Market(s)

adult that have money :)

Industry/Entity Type

Business

Contact Information for Business Card

Name - Dario Lorvanti
Position - CEO and CO Founder
address - 4817 E Halvern
telephone - 555-384-1926
email - dario@lorvanti.com
fax - 555-384-1926
website - LORVANTI.COM

Colors
000000
959595
fbee3e
ffffff

Requirements
Must have
• big logo in GOLD color
• elegant look
• impressive
Nice to have
• not must but maybe classy pattern background
• not must but maybe emblem
• maybe clear plastic business card
Should not have
• colors
• images

```html
<!DOCTYPE html>
<html lang="en">
<head>
<meta charset="utf-8">
<title>LORVANTI Italy – Business Card</title>
<link href="https://fonts.googleapis.com/css2?family=Cormorant+Garamond:wght@500&family=Nanum+Gothic:wght@400;700&display=swap" rel="stylesheet">
<style>
  :root {
    --backdrop: #3b3632;
    --card-black: #141312;
    --card-edge: #232120;
    --gold: #e0b63a;
    --pattern-tone: #4a4744;
  }
  * { box-sizing: border-box; margin: 0; padding: 0; }
  html, body { width: 1200px; height: 1200px; overflow: hidden; }
  body {
    background: var(--backdrop);
    display: flex;
    flex-direction: column;
    align-items: center;
    justify-content: center;
    gap: 44px;
    font-family: "Nanum Gothic", sans-serif;
  }
  .card {
    position: relative;
    width: 840px;
    height: 480px;
    border-radius: 22px;
    background: radial-gradient(ellipse at 60% 40%, var(--card-edge), var(--card-black) 75%);
    overflow: hidden;
    box-shadow: 0 14px 30px rgba(0,0,0,.45);
    color: var(--gold);
  }
  .card__pattern {
    position: absolute;
    top: -60px;
    width: 560px;
    height: 600px;
    border-radius: 50%;
    background: radial-gradient(circle, transparent 44%, var(--pattern-tone) 46%, rgba(74,71,68,.55) 62%, transparent 64%);
    opacity: .55;
  }
  .card--front .card__pattern { left: -330px; }
  .card--back .card__pattern { left: -300px; }

  .brand { position: absolute; text-align: center; }
  .brand__seal {
    display: block;
    margin: 0 auto;
    border: 4px solid var(--gold);
    border-radius: 50%;
  }
  .brand__name, .brand__place {
    font-family: "Cormorant Garamond", serif;
    font-weight: 500;
    color: var(--gold);
    letter-spacing: .02em;
  }
  .card--front .brand { left: 190px; right: 110px; top: 60px; }
  .card--front .brand__seal { width: 140px; height: 140px; }
  .card--front .brand__name { font-size: 96px; line-height: 1; margin-top: 40px; }
  .card--front .brand__place { font-size: 30px; margin-top: 10px; }

  .card--back .brand { right: 60px; top: 40px; width: 300px; }
  .card--back .brand__seal { width: 104px; height: 104px; }
  .card--back .brand__name { font-size: 58px; line-height: 1; margin-top: 26px; }
  .card--back .brand__place { font-size: 22px; margin-top: 6px; }

  .person { position: absolute; left: 60px; top: 232px; }
  .person__name { font-size: 38px; font-weight: 700; }
  .person__role { font-size: 20px; margin-top: 8px; }

  .divider {
    position: absolute;
    left: 60px; right: 60px; top: 310px;
    height: 3px;
    background: var(--gold);
  }

  .contacts {
    position: absolute;
    left: 60px; right: 40px; top: 340px;
    display: grid;
    grid-template-columns: 250px 245px 1fr;
    row-gap: 28px;
    list-style: none;
    font-size: 20px;
  }
  .contact { display: flex; align-items: center; gap: 12px; white-space: nowrap; }
  .contact__icon { width: 34px; height: 34px; flex: none; }
</style>
</head>
<body>

<section class="card card--front" aria-label="Card front">
  <div class="card__pattern" role="img" aria-label="Faint ornamental ring pattern"></div>
  <div class="brand">
    <span class="brand__seal"></span>
    <p class="brand__name">LORVANTI</p>
    <p class="brand__place">ITALY</p>
  </div>
</section>

<section class="card card--back" aria-label="Card back">
  <div class="card__pattern" role="img" aria-label="Faint ornamental ring pattern"></div>

  <div class="brand">
    <span class="brand__seal"></span>
    <p class="brand__name">LORVANTI</p>
    <p class="brand__place">ITALY</p>
  </div>

  <div class="person">
    <p class="person__name">Dario Lorvanti</p>
    <p class="person__role">CEO and CO Founder</p>
  </div>

  <div class="divider"></div>

  <ul class="contacts">
    <li class="contact">
      <svg class="contact__icon" viewBox="0 0 34 34" fill="none" stroke="currentColor" stroke-width="2">
        <circle cx="17" cy="17" r="15"/>
        <path d="M17 26c-4-5-6-8-6-11a6 6 0 0 1 12 0c0 3-2 6-6 11z" fill="currentColor" stroke="none"/>
        <circle cx="17" cy="15" r="2.2" fill="#141312" stroke="none"/>
      </svg>
      4817 E Halvern
    </li>
    <li class="contact">
      <svg class="contact__icon" viewBox="0 0 34 34" fill="none" stroke="currentColor" stroke-width="2">
        <circle cx="17" cy="17" r="15"/>
        <path d="M11 10l4 0 1.5 4-2 1.5a9 9 0 0 0 4 4l1.5-2 4 1.5v4c-8 0-13-5-13-13z" fill="currentColor" stroke="none"/>
      </svg>
      555-384-1926
    </li>
    <li class="contact">
      <svg class="contact__icon" viewBox="0 0 34 34" fill="none" stroke="currentColor" stroke-width="2">
        <circle cx="17" cy="17" r="15"/>
        <rect x="9" y="11" width="16" height="12" fill="currentColor" stroke="none"/>
        <path d="M10 12l7 6 7-6" stroke="#141312" stroke-width="1.6"/>
      </svg>
      dario@lorvanti.com
    </li>
    <li class="contact">
      <svg class="contact__icon" viewBox="0 0 34 34" fill="none" stroke="currentColor" stroke-width="2">
        <circle cx="17" cy="17" r="15"/>
        <rect x="9" y="14" width="16" height="10" rx="1" fill="currentColor" stroke="none"/>
        <rect x="12" y="9" width="10" height="6" stroke-width="1.6"/>
      </svg>
      555-384-1926
    </li>
    <li class="contact">
      <svg class="contact__icon" viewBox="0 0 34 34" fill="none" stroke="currentColor" stroke-width="2">
        <circle cx="17" cy="17" r="15"/>
        <circle cx="17" cy="17" r="8" stroke-width="1.6"/>
        <path d="M9 17h16M17 9c-3 3-3 13 0 16M17 9c3 3 3 13 0 16" stroke-width="1.4"/>
      </svg>
      lorvanti.com
    </li>
  </ul>
</section>

</body>
</html>
```